Business Card Design for Property Development Company Director

I am looking for a professional and unforgettable business card design for our Director of our Property Development Company.
Please see attached .pptx file to find out what information to include. You don't have to follow the exact format shown in the file - I am interested to see your creative flair using the information provided.

```html
<!DOCTYPE html>
<html lang="en">
<head>
<meta charset="utf-8">
<title>Norvale Property Group – Business Card</title>
<link href="https://fonts.googleapis.com/css2?family=Roboto:wght@400;500;700&family=Roboto+Condensed:wght@700&display=swap" rel="stylesheet">
<style>
  :root {
    --page: #e4e5e7;
    --brand-blue: #2b4c8f;
    --brand-blue-dark: #1f3a73;
    --slate: #4d5159;
    --card-white: #f4f4f4;
    --ink-soft: #5a5e66;
    --white: #ffffff;
  }
  * { margin: 0; padding: 0; box-sizing: border-box; }
  html, body { width: 1200px; height: 726px; overflow: hidden; }
  body {
    background: var(--page);
    font-family: "Roboto", Arial, sans-serif;
    display: flex;
    align-items: center;
    justify-content: center;
    gap: 50px;
  }
  .card {
    position: relative;
    width: 540px;
    height: 309px;
    overflow: hidden;
    flex: 0 0 auto;
    box-shadow: 0 6px 18px rgba(0,0,0,0.18);
  }

  /* Front side */
  .card--front {
    background: var(--brand-blue);
    color: var(--white);
    text-align: center;
  }
  .front__tagline {
    position: absolute;
    top: 34px; left: 0; right: 0;
    font-size: 17px;
    line-height: 1.25;
  }
  .front__brand {
    position: absolute;
    top: 134px; left: 0; right: 0;
    display: flex;
    align-items: center;
    justify-content: center;
    gap: 14px;
  }
  .brand-square {
    flex: 0 0 auto;
    width: 30px; height: 30px;
    background: var(--white);
  }
  .front__brand .brand-name {
    font-size: 28px;
    font-weight: 700;
    letter-spacing: 0.5px;
    line-height: 1;
    white-space: nowrap;
    text-transform: uppercase;
  }
  .front__invite {
    position: absolute;
    bottom: 36px; left: 0; right: 0;
    font-size: 15px;
  }

  /* Back side */
  .card--back { background: var(--card-white); }
  .back__waves { position: absolute; inset: 0; }
  .back__person {
    position: absolute;
    top: 24px; right: 30px;
    text-align: right;
  }
  .person__name {
    font-family: "Roboto Condensed", "Arial Narrow", sans-serif;
    font-weight: 700;
    font-size: 19px;
    color: var(--brand-blue);
  }
  .person__role {
    font-size: 11px;
    color: var(--ink-soft);
    margin-top: 2px;
  }
  .back__brand {
    position: absolute;
    top: 112px; left: 34px;
    display: flex;
    align-items: center;
    gap: 12px;
  }
  .back__brand .brand-square { background: var(--slate); width: 26px; height: 26px; }
  .back__brand .brand-name {
    font-size: 22px;
    font-weight: 700;
    color: var(--slate);
    text-transform: uppercase;
    letter-spacing: 0.5px;
    line-height: 1.1;
  }
  .back__contact {
    position: absolute;
    right: 24px; top: 150px;
    list-style: none;
    text-align: right;
    color: var(--white);
    font-size: 13px;
    line-height: 1.55;
  }
  .back__contact li {
    display: flex;
    justify-content: flex-end;
    align-items: center;
    gap: 6px;
  }
  .contact-icon { width: 11px; height: 11px; fill: var(--white); }
</style>
</head>
<body>

  <section class="card card--front" aria-label="Card front">
    <p class="front__tagline">Property Development<br>&amp; Site Acquisition Specialists</p>
    <div class="front__brand">
      <span class="brand-square"></span>
      <span class="brand-name">Norvale Property Group</span>
    </div>
    <p class="front__invite">Ask me about our INVESTMENT &amp; PARTNERSHIP opportunities</p>
  </section>

  <section class="card card--back" aria-label="Card back">
    <svg class="back__waves" width="540" height="309" viewBox="0 0 540 309" aria-hidden="true">
      <path d="M0 268 C120 292 230 282 290 200 S440 92 540 86 L540 309 L0 309 Z" fill="var(--brand-blue)"/>
      <path d="M0 268 C120 292 230 282 290 200 S440 92 540 86" transform="translate(0,-10)" fill="none" stroke="var(--slate)" stroke-width="7"/>
      <path d="M60 309 C170 290 260 270 310 215 S460 110 540 104" fill="none" stroke="var(--brand-blue-dark)" stroke-width="3" opacity="0.6"/>
    </svg>

    <div class="back__person">
      <p class="person__name">Daniel Marsh</p>
      <p class="person__role">Director</p>
    </div>

    <div class="back__brand">
      <span class="brand-square"></span>
      <span class="brand-name">Norvale<br>Property Group</span>
    </div>

    <ul class="back__contact">
      <li>0400 321 765
        <svg class="contact-icon" viewBox="0 0 12 12"><path d="M3 1l2 2.5-1.2 1.2a7 7 0 003.5 3.5L8.5 7 11 9l-1.5 2C5 11 1 7 1 2.5z"/></svg>
      </li>
      <li>www.norvale.com.au
        <svg class="contact-icon" viewBox="0 0 12 12"><circle cx="6" cy="6" r="5" fill="none" stroke="#fff" stroke-width="1.4"/><path d="M1 6h10M6 1c-2 3-2 7 0 10M6 1c2 3 2 7 0 10" fill="none" stroke="#fff" stroke-width="1"/></svg>
      </li>
      <li>daniel@norvale.com.au
        <svg class="contact-icon" viewBox="0 0 12 12"><rect x="0.5" y="2.5" width="11" height="7" fill="none" stroke="#fff" stroke-width="1.2"/><path d="M0.5 2.5L6 7l5.5-4.5" fill="none" stroke="#fff" stroke-width="1.2"/></svg>
      </li>
      <li>Real Estate Lic: 5512093 &amp; 5512094</li>
    </ul>
  </section>

</body>
</html>
```